Mortgage Broking Flyer to attract attention

We are looking for double sided, colour DL sized flyers for a mail drop to inform people what services we offer.
We are a Mortgage Broking Business in Alice Springs NT Australia. Alice Springs is a large country town so we want something that is personal, a little bit playful but still professional, and is going to capture the attention of potential clients when they first look at it so they want to read on.
Please use our logo and colours (red & white) plus a photo of our team – all attached.
Brochure Front: IMPORTANT
Please come up with a tag line based on the following-We want to be seen as different to the bank, more friendly, personable, we listen, want to help and want people to keep coming back even for the little things.
The home page from our website has good dot points but we would like them shorter and to the point www.ochrecrestlending.com.au
Plus include something which lets customer know that we can assist purchases made through any real estate office, anywhere in Australia
Don’t want the front to contain too many long sentences or paragraphs.
Brochure Back:
Please include:
Services/Specialties
• First home buyers
• Refinancing
• Investments
• Construction loans
• Debt consolidation
• Commercial finance
Please include the following contact details:
Dominic Farrow – Managing Director
Prudence Wexley – Loans Consultant
Maeve Dunleavy – Loans Consultant
Suite 4/17 Corbel Street, Alice Springs NT 0870
Phone: 08 8961 4728
www.ochrecrestlending.com.au
We must include the following fine print at the back/bottom of the brochure:
Dominic Farrow (Credit Representative Number: 527814), Prudence Wexley (Credit Representative Number: 527813) and Maeve Dunleavy (Credit Representative Number: 613290) are credit representatives of QMTRV Pty Ltd (Australian Credit Licence Number: 458906)
Please feel free to email me with any questions.
maeve@ochrecrestlending.com.au

```html
<!DOCTYPE html>
<html lang="en">
<head>
<meta charset="utf-8">
<title>Ochre Crest Lending – DL Flyer</title>
<link href="https://fonts.googleapis.com/css2?family=Oswald:wght@300;500&family=Roboto+Condensed:wght@300;400;700&family=Open+Sans:ital,wght@0,400;0,600;1,400&display=swap" rel="stylesheet">
<style>
:root{
  --red:#d71920;
  --red-dark:#a90f15;
  --black:#151515;
  --white:#ffffff;
  --grey-light:#ececec;
  --grey-mid:#c9c9c9;
  --ink:#222222;
  --stage:#e4e4e4;
}
*{box-sizing:border-box;margin:0;padding:0}
html,body{width:1200px;height:1200px;overflow:hidden}
body{background:var(--stage);font-family:"Open Sans",sans-serif;position:relative}
.flyer{position:absolute;top:148px;width:440px;height:905px;overflow:hidden;background:var(--white);box-shadow:0 6px 18px rgba(0,0,0,.18)}
.flyer--front{left:140px}
.flyer--back{left:620px}
.flyer svg.art{position:absolute;inset:0}
.abs{position:absolute}

/* front */
.brand{left:40px;top:52px;display:flex;align-items:center;gap:16px}
.brand__dot{width:52px;height:52px;border-radius:50%;background:var(--red)}
.brand__name{font-family:"Roboto Condensed",sans-serif;font-weight:300;font-size:36px;color:var(--ink);letter-spacing:.5px}
.tagline{left:22px;top:436px;width:390px;height:152px;border-radius:22px;background:var(--black);border:4px solid #8a8a8a;padding:14px 24px;font-family:"Oswald",sans-serif;line-height:1}
.tagline__line1{font-size:62px;font-weight:500;color:var(--white)}
.tagline__line1 .accent{color:var(--red);font-weight:300}
.tagline__line2{font-size:56px;font-weight:500;color:var(--white);margin-top:6px}
.tagline__line2 .accent{color:var(--red);font-weight:300}
.website{right:36px;bottom:20px;text-align:right;color:var(--white);font-size:16px;font-weight:600;line-height:1.35}

/* back */
.services{left:28px;top:236px;width:384px;height:148px;border-radius:26px;background:var(--black);padding:12px 22px;color:var(--white);font-family:"Roboto Condensed",sans-serif}
.services__title{text-align:center;color:var(--red);font-size:24px;margin-bottom:6px}
.services__cols{display:flex;justify-content:space-between}
.services__list{list-style:none;font-size:19px;line-height:1.3}
.services__list li::before{content:"";display:inline-block;width:8px;height:8px;border-radius:50%;background:var(--red);margin-right:7px;vertical-align:middle}
.team{left:20px;top:416px;width:400px;display:flex;justify-content:space-between;font-family:"Roboto Condensed",sans-serif}
.team__member{padding:0 6px;border-left:2px solid var(--red)}
.team__member:first-child{border-left:none}
.team__name{color:var(--red);font-size:15px;font-weight:700}
.team__role{font-style:italic;color:var(--ink);font-size:14px}
.contact{left:0;top:484px;width:440px;text-align:center;font-family:"Roboto Condensed",sans-serif;color:var(--ink)}
.contact__phone{font-size:28px;font-weight:700}
.contact__phone .label{color:var(--red)}
.contact__address{font-size:16px;font-weight:700;margin-top:2px}
.fineprint{left:24px;top:566px;width:392px;border:3px solid var(--red);border-radius:24px;padding:12px 16px;font-size:11.5px;line-height:1.4;text-align:justify;color:var(--ink);background:var(--white)}
.seal{left:18px;top:700px;width:170px;height:170px;border-radius:50%;background:var(--red);border:10px solid var(--white);box-shadow:0 0 0 3px var(--red)}
.invite{right:30px;top:790px;text-align:right;font-family:"Roboto Condensed",sans-serif;color:var(--black);line-height:1.1}
.invite__a{font-size:24px;font-weight:700}
.invite__b{font-size:24px;font-weight:400}
.invite__c{font-size:28px;font-weight:700}
</style>
</head>
<body>

<section class="flyer flyer--front" aria-label="Flyer front">
  <svg class="art" viewBox="0 0 440 905" width="440" height="905">
    <defs>
      <linearGradient id="bgGrey" x1="0" y1="0" x2="0" y2="1">
        <stop offset="0" stop-color="#f4f4f4"/><stop offset="1" stop-color="#d6d6d6"/>
      </linearGradient>
      <linearGradient id="teamTone" x1="0" y1="0" x2="1" y2="0">
        <stop offset="0" stop-color="#8b6f66"/><stop offset=".5" stop-color="#d9d6d6"/><stop offset="1" stop-color="#2b3a7a"/>
      </linearGradient>
    </defs>
    <rect y="140" width="440" height="765" fill="url(#bgGrey)"/>
    <path d="M0,115 C140,150 300,175 440,140 L440,175 C300,200 140,180 0,150 Z" fill="var(--red)"/>
    <path d="M0,150 C140,180 300,200 440,175 L440,390 C300,360 140,355 0,345 Z" fill="url(#teamTone)" role="img" aria-label="Photo of the three-person lending team"/>
    <path d="M0,345 C140,355 300,360 440,390 L440,415 C300,400 140,400 0,370 Z" fill="var(--red)"/>
    <circle cx="128" cy="686" r="77" fill="var(--red)"/>
    <circle cx="128" cy="686" r="72" fill="#5b6f8c" role="img" aria-label="Photo of a handshake over a model house"/>
    <circle cx="306" cy="686" r="77" fill="var(--red)"/>
    <circle cx="306" cy="686" r="72" fill="#3d4350" role="img" aria-label="Photo of a hand selecting a mortgage menu"/>
    <path d="M0,760 C150,830 300,780 440,740 L440,905 L0,905 Z" fill="#bdbdbd"/>
    <path d="M0,790 C150,855 300,810 440,775 L440,905 L0,905 Z" fill="var(--red)"/>
    <path d="M0,850 C150,880 320,850 440,820 L440,905 L0,905 Z" fill="var(--red-dark)"/>
  </svg>
  <div class="abs brand">
    <span class="brand__dot"></span>
    <span class="brand__name">OCHRE CREST LENDING</span>
  </div>
  <div class="abs tagline">
    <div class="tagline__line1">It All <span class="accent">Begins</span></div>
    <div class="tagline__line2"><span class="accent">WITH</span> SUCCESS</div>
  </div>
  <div class="abs website">Website:<br>www.ochrecrestlending.com.au</div>
</section>

<section class="flyer flyer--back" aria-label="Flyer back">
  <svg class="art" viewBox="0 0 440 905" width="440" height="905">
    <defs>
      <linearGradient id="bgGrey2" x1="0" y1="0" x2="0" y2="1">
        <stop offset="0" stop-color="#dcdcdc"/><stop offset="1" stop-color="#f6f6f6"/>
      </linearGradient>
    </defs>
    <rect width="440" height="905" fill="url(#bgGrey2)"/>
    <path d="M0,0 L440,0 L440,140 C300,70 150,60 0,110 Z" fill="var(--red)"/>
    <path d="M0,110 C150,60 300,70 440,140 L440,175 C300,105 150,95 0,140 Z" fill="#a8a8a8"/>
    <circle cx="140" cy="110" r="82" fill="var(--red)"/>
    <circle cx="140" cy="110" r="77" fill="#8ea0b4" role="img" aria-label="Photo of two consultants at a computer"/>
    <circle cx="320" cy="130" r="82" fill="var(--red)"/>
    <circle cx="320" cy="130" r="77" fill="#2f4f86" role="img" aria-label="Photo of a finger pressing a business loan button"/>
    <path d="M0,905 L0,820 C150,800 300,760 440,700 L440,905 Z" fill="var(--white)"/>
    <path d="M150,790 C260,770 360,735 440,700 L440,740 C360,770 260,800 150,815 Z" fill="var(--red)"/>
    <path d="M150,815 C260,800 360,770 440,740 L440,755 C360,785 260,815 150,825 Z" fill="#9a9a9a"/>
  </svg>

  <div class="abs services">
    <div class="services__title">Services</div>
    <div class="services__cols">
      <ul class="services__list">
        <li>First home buyers</li>
        <li>Refinancing</li>
        <li>Investments</li>
      </ul>
      <ul class="services__list">
        <li>Construction loans</li>
        <li>Debt consolidation</li>
        <li>Commercial finance</li>
      </ul>
    </div>
  </div>

  <div class="abs team">
    <div class="team__member"><div class="team__name">Dominic Farrow</div><div class="team__role">Managing Director</div></div>
    <div class="team__member"><div class="team__name">Prudence Wexley</div><div class="team__role">Loans Consultant</div></div>
    <div class="team__member"><div class="team__name">Maeve Dunleavy</div><div class="team__role">Loans Consultant</div></div>
  </div>

  <div class="abs contact">
    <div class="contact__phone"><span class="label">Phone:</span> 08 8961 4728</div>
    <div class="contact__address">Suite 4/17 Corbel Street, Alice Springs NT 0870</div>
  </div>

  <p class="abs fineprint">Dominic Farrow (Credit Representative Number: 527814), Prudence Wexley (Credit Representative Number: 527813) and Maeve Dunleavy (Credit Representative Number: 613290) are credit representatives of QMTRV Pty Ltd (Australian Credit Licence Number: 458906)</p>

  <div class="abs seal"></div>
  <div class="abs invite">
    <div class="invite__a">Please feel free</div>
    <div class="invite__b">to email me with</div>
    <div class="invite__c">any questions</div>
  </div>
</section>

</body>
</html>
```